R7M Horizon Business Card Design

We need a business card created for our New Business "R7M Horizon"<br/><br/>The business card design is up to you however the following information must be on the business card:<br/><br/>Front of the business card -<br/>Email :darrenp@r7mhorizon.nz<br/>Mobile: +64 (0) 22 4870 619<br/>Website: www.r7mhorizon.nz<br/>Card Owner Name: Darren Paltrow<br/>Company Title: Business Development Manager<br/>Slogan: "The BEST of both worlds". <br/>Logo On the front attached to the design brief<br/><br/>On the back: <br/>Space on the back for 4 more versions of the logo across the bottom of the card indicating different subsidiary brands - R7M Coffee, R7M Arts, R7M ?? (The card will be used for all of these brands - We Will add the extra subsidiary logos to the design once the design is finished (We are a graphics design team). <br/><br/>Other than that we want a premium feeling logo that remains universally usable depending on the business entity that we are using the card for. The use of bright bold colours would be great but we still want the card to feel premium.
Target Market(s)
Gift Design and Manufacturing Companies
Contact Information for Business Card
Front of the business card -
Email :darrenp@r7mhorizon.nz
Mobile: +64 (0) 22 4870 619
Website: www.r7mhorizon.nz
Card Owner Name: Darren Paltrow
Company Title: Business Development Manager
Slogan: "The BEST of both worlds".
Logo On the front attached to the design brief

```html
<!DOCTYPE html>
<html lang="en">
<head>
<meta charset="utf-8">
<title>R7M Horizon Business Card</title>
<link href="https://fonts.googleapis.com/css2?family=Michroma&family=Open+Sans:wght@400;700&display=swap" rel="stylesheet">
<style>
  :root {
    --brand-blue: #3a46a6;
    --brand-blue-deep: #2f3a96;
    --ink: #222630;
    --paper: #ffffff;
    --backdrop: #2b2c2f;
    --ghost: #eef0f8;
  }
  * { margin: 0; padding: 0; box-sizing: border-box; }
  html, body { width: 1200px; height: 900px; overflow: hidden; }
  body {
    background: var(--backdrop);
    font-family: "Open Sans", sans-serif;
    position: relative;
  }
  .card {
    position: absolute;
    left: 280px;
    width: 640px;
    height: 366px;
    border-radius: 18px;
    overflow: hidden;
  }
  /* Back side */
  .card--back {
    top: 38px;
    background: linear-gradient(135deg, var(--brand-blue-deep), var(--brand-blue) 60%, #4a55b4);
  }
  .back-mark {
    position: absolute;
    left: 0; right: 0; top: 120px;
    display: flex; justify-content: center; align-items: center; gap: 18px;
  }
  .back-mark__name {
    font-family: "Michroma", sans-serif;
    font-size: 40px;
    color: #5562c2;
    letter-spacing: 1px;
  }
  .back-mark__dot {
    width: 46px; height: 46px; border-radius: 50%;
    border: 4px solid #5562c2;
  }
  .back-web {
    position: absolute;
    left: 0; right: 0; bottom: 40px;
    text-align: center;
    color: var(--paper);
    font-size: 17px;
    letter-spacing: 1.5px;
  }
  /* Front side */
  .card--front {
    top: 476px;
    background: var(--paper);
  }
  .ghost-name {
    position: absolute;
    left: 290px; top: 70px;
    font-family: "Michroma", sans-serif;
    font-size: 120px;
    color: var(--ghost);
    white-space: nowrap;
    line-height: 1;
  }
  .front-mark {
    position: absolute;
    left: 26px; top: 34px;
    display: flex; align-items: center; gap: 10px;
  }
  .front-mark__name {
    font-family: "Michroma", sans-serif;
    font-size: 22px;
    color: var(--brand-blue);
  }
  .front-mark__dot {
    width: 30px; height: 30px; border-radius: 50%;
    border: 4px solid var(--brand-blue);
  }
  .slogan-band {
    position: absolute;
    left: 168px; top: 100px; bottom: 0;
    width: 62px;
    background: var(--brand-blue);
  }
  .slogan-band__text {
    position: absolute;
    left: 50%; top: 50%;
    transform: translate(-50%, -50%) rotate(-90deg);
    white-space: nowrap;
    color: var(--paper);
    font-size: 20px;
  }
  .slogan-band__text strong { font-weight: 700; }
  .person {
    position: absolute;
    left: 300px; top: 150px;
  }
  .person__name {
    font-family: "Michroma", sans-serif;
    font-size: 24px;
    color: var(--brand-blue);
    text-transform: uppercase;
    white-space: nowrap;
  }
  .person__title {
    font-size: 16px;
    color: var(--ink);
    margin-top: 4px;
  }
  .person__rule {
    width: 28px; height: 2px;
    background: var(--brand-blue);
    margin: 16px 0 18px;
  }
  .contacts { list-style: none; }
  .contacts li {
    display: flex; align-items: center; gap: 12px;
    font-size: 17px;
    color: var(--ink);
    line-height: 28px;
  }
  .contacts svg { width: 14px; height: 14px; flex: none; }
</style>
</head>
<body>

<section class="card card--back">
  <div class="back-mark">
    <span class="back-mark__name">R7M HORIZON</span>
    <span class="back-mark__dot"></span>
  </div>
  <p class="back-web">www.r7mhorizon.nz</p>
</section>

<section class="card card--front">
  <div class="ghost-name" aria-hidden="true">R7M</div>

  <div class="front-mark">
    <span class="front-mark__name">R7M HORIZON</span>
    <span class="front-mark__dot"></span>
  </div>

  <div class="slogan-band">
    <p class="slogan-band__text">The <strong>BEST</strong> of both worlds</p>
  </div>

  <div class="person">
    <h1 class="person__name">Darren Paltrow</h1>
    <p class="person__title">Business Development Manager</p>
    <div class="person__rule"></div>
    <ul class="contacts">
      <li>
        <svg viewBox="0 0 14 14"><path d="M3 1h3l1 3-2 1.5a8 8 0 0 0 3.5 3.5L10 7l3 1v3a2 2 0 0 1-2 2A10 10 0 0 1 1 3a2 2 0 0 1 2-2z" fill="var(--brand-blue)"/></svg>
        +64 (0) 22 4870 619
      </li>
      <li>
        <svg viewBox="0 0 14 14"><rect x="1" y="3" width="12" height="8" fill="none" stroke="var(--brand-blue)" stroke-width="1.4"/><path d="M1 3l6 5 6-5" fill="none" stroke="var(--brand-blue)" stroke-width="1.4"/></svg>
        darrenp@r7mhorizon.nz
      </li>
      <li>
        <svg viewBox="0 0 14 14"><circle cx="7" cy="7" r="6" fill="none" stroke="var(--brand-blue)" stroke-width="1.3"/><ellipse cx="7" cy="7" rx="2.6" ry="6" fill="none" stroke="var(--brand-blue)" stroke-width="1.1"/><path d="M1 7h12M2 4h10M2 10h10" stroke="var(--brand-blue)" stroke-width="1"/></svg>
        www.r7mhorizon.nz
      </li>
    </ul>
  </div>
</section>

</body>
</html>
```